New Business Card Design Project

Use the flyer uploaded and website www.brightoakbuilders.com for inspiration.
List Our Services on Backside of business cards
Marcus Delling
Harborline Builders Inc.
Licensed General Contractors
858-471-6093

Contact Information for Business Card

Use the flyer uploaded and website www.brightoakbuilders.com for inspiration. List Our Services on Backside of business cards Marcus Delling Harborline Builders Inc. Licensed General Contractors 858-471-6093

```html
<!DOCTYPE html>
<html lang="en">
<head>
<meta charset="UTF-8">
<title>Harborline Builders – Business Card</title>
<link href="https://fonts.googleapis.com/css2?family=Open+Sans:wght@400;600&family=Roboto:wght@700;900&display=swap" rel="stylesheet">
<style>
  :root {
    --backdrop: #222223;
    --card: #1d1d20;
    --ink: #f2f2f2;
    --muted: #cfcfd2;
    --accent-red: #e3202a;
    --accent-blue: #4f7fd6;
    --rule: #d8d8d8;
  }
  html, body {
    margin: 0;
    width: 1200px;
    height: 780px;
    overflow: hidden;
    background: var(--backdrop);
    font-family: "Open Sans", Arial, sans-serif;
  }
  .canvas {
    position: relative;
    width: 1200px;
    height: 780px;
  }
  .card {
    position: absolute;
    top: 231px;
    width: 555px;
    height: 318px;
    background: var(--card);
    border-radius: 22px;
    box-shadow: 0 10px 30px rgba(0,0,0,.45);
    overflow: hidden;
    color: var(--ink);
  }
  .card--front { left: 30px; }
  .card--back { left: 615px; }

  .brand {
    position: absolute;
    display: flex;
    align-items: center;
    gap: 9px;
    font-size: 18px;
    font-weight: 400;
    letter-spacing: 1.5px;
    white-space: nowrap;
    text-transform: uppercase;
    color: var(--ink);
  }
  .brand__mark {
    width: 12px;
    height: 12px;
    border: 1.5px solid var(--ink);
  }
  .card--front .brand { left: 36px; top: 70px; }
  .card--back .brand { left: 32px; top: 92px; }

  .divider {
    position: absolute;
    left: 180px;
    top: 122px;
  }
  .company-legal {
    position: absolute;
    left: 40px;
    bottom: 40px;
    font-size: 14px;
    color: var(--ink);
  }

  .person {
    position: absolute;
    left: 292px;
    top: 118px;
  }
  .person__name {
    font-family: "Roboto", Arial, sans-serif;
    font-weight: 900;
    font-size: 25px;
    letter-spacing: .3px;
    white-space: nowrap;
    text-transform: uppercase;
    color: var(--accent-red);
    margin: 0;
    line-height: 1;
  }
  .person__title {
    font-size: 14px;
    margin: 6px 0 16px;
    color: var(--ink);
  }
  .contact {
    list-style: none;
    margin: 0;
    padding: 0;
  }
  .contact__item {
    display: flex;
    align-items: center;
    gap: 10px;
    font-size: 14px;
    line-height: 26px;
    white-space: nowrap;
    color: var(--ink);
  }
  .contact__icon { width: 15px; height: 15px; flex: none; }

  .services {
    position: absolute;
    left: 330px;
    top: 40px;
  }
  .services__guarantee {
    font-family: "Roboto", Arial, sans-serif;
    font-weight: 900;
    font-size: 15px;
    font-style: italic;
    text-transform: uppercase;
    color: var(--accent-red);
    margin: 0;
    line-height: 1.15;
  }
  .services__lead {
    font-family: "Roboto", Arial, sans-serif;
    font-weight: 900;
    font-size: 15px;
    font-style: italic;
    text-transform: uppercase;
    color: var(--accent-blue);
    margin: 2px 0 8px;
  }
  .services__list {
    list-style: none;
    margin: 0;
    padding: 0;
  }
  .services__item {
    display: flex;
    align-items: center;
    gap: 8px;
    font-size: 12.5px;
    font-weight: 600;
    line-height: 20.5px;
    white-space: nowrap;
    color: var(--ink);
  }
  .services__tick { width: 13px; height: 13px; flex: none; }
</style>
</head>
<body>
<div class="canvas">

  <section class="card card--front" aria-label="Business card front">
    <div class="brand"><span class="brand__mark"></span>Harborline Builders</div>
    <svg class="divider" width="100" height="120" viewBox="0 0 100 120" aria-hidden="true">
      <line x1="98" y1="2" x2="2" y2="118" stroke="var(--rule)" stroke-width="1"/>
    </svg>
    <div class="company-legal">Harborline Builders Inc.</div>

    <div class="person">
      <h1 class="person__name">Marcus Delling</h1>
      <p class="person__title">Licensed General Contractors</p>
      <ul class="contact">
        <li class="contact__item">
          <svg class="contact__icon" viewBox="0 0 16 16" aria-hidden="true"><path d="M4 1.5l2.2 3-1.3 1.6c.8 1.9 2.3 3.4 4.2 4.2l1.6-1.3 3 2.2-1.2 2.6C6.8 13.6 2.4 9.2 1.4 2.7z" fill="var(--accent-red)"/></svg>
          858-471-6093
        </li>
        <li class="contact__item">
          <svg class="contact__icon" viewBox="0 0 16 16" aria-hidden="true"><rect x="1" y="3" width="14" height="10" rx="2" fill="var(--accent-red)"/><path d="M2 4.5l6 4.5 6-4.5" stroke="var(--card)" stroke-width="1.3" fill="none"/></svg>
          info@brightoakbuilders.com
        </li>
        <li class="contact__item">
          <svg class="contact__icon" viewBox="0 0 16 16" aria-hidden="true"><circle cx="8" cy="8" r="7" fill="var(--accent-red)"/><path d="M1 8h14M8 1c-2.5 3-2.5 11 0 14M8 1c2.5 3 2.5 11 0 14" stroke="var(--card)" stroke-width="1" fill="none"/></svg>
          www.brightoakbuilders.com
        </li>
      </ul>
    </div>
  </section>

  <section class="card card--back" aria-label="Business card back">
    <div class="brand"><span class="brand__mark"></span>Harborline Builders</div>

    <div class="services">
      <p class="services__guarantee">Our services are<br>100% guaranteed</p>
      <p class="services__lead">Specializing in:</p>
      <ul class="services__list">
        <li class="services__item"><svg class="services__tick" viewBox="0 0 14 14" aria-hidden="true"><circle cx="7" cy="7" r="6" fill="none" stroke="var(--accent-red)" stroke-width="1.4"/><path d="M4 7.2l2 2 4-4.4" fill="none" stroke="var(--accent-red)" stroke-width="1.6"/></svg>Remodel: Kitchen &amp; Bath</li>
        <li class="services__item"><svg class="services__tick" viewBox="0 0 14 14" aria-hidden="true"><circle cx="7" cy="7" r="6" fill="none" stroke="var(--accent-red)" stroke-width="1.4"/><path d="M4 7.2l2 2 4-4.4" fill="none" stroke="var(--accent-red)" stroke-width="1.6"/></svg>Painting: Interior &amp; Exterior</li>
        <li class="services__item"><svg class="services__tick" viewBox="0 0 14 14" aria-hidden="true"><circle cx="7" cy="7" r="6" fill="none" stroke="var(--accent-red)" stroke-width="1.4"/><path d="M4 7.2l2 2 4-4.4" fill="none" stroke="var(--accent-red)" stroke-width="1.6"/></svg>Flooring: Carpet, Vinyl, Wood</li>
        <li class="services__item"><svg class="services__tick" viewBox="0 0 14 14" aria-hidden="true"><circle cx="7" cy="7" r="6" fill="none" stroke="var(--accent-red)" stroke-width="1.4"/><path d="M4 7.2l2 2 4-4.4" fill="none" stroke="var(--accent-red)" stroke-width="1.6"/></svg>Window &amp; Door Replacement</li>
        <li class="services__item"><svg class="services__tick" viewBox="0 0 14 14" aria-hidden="true"><circle cx="7" cy="7" r="6" fill="none" stroke="var(--accent-red)" stroke-width="1.4"/><path d="M4 7.2l2 2 4-4.4" fill="none" stroke="var(--accent-red)" stroke-width="1.6"/></svg>Plumbing: Repairs &amp; Upgrades</li>
        <li class="services__item"><svg class="services__tick" viewBox="0 0 14 14" aria-hidden="true"><circle cx="7" cy="7" r="6" fill="none" stroke="var(--accent-red)" stroke-width="1.4"/><path d="M4 7.2l2 2 4-4.4" fill="none" stroke="var(--accent-red)" stroke-width="1.6"/></svg>Energy-Efficient Upgrades</li>
        <li class="services__item"><svg class="services__tick" viewBox="0 0 14 14" aria-hidden="true"><circle cx="7" cy="7" r="6" fill="none" stroke="var(--accent-red)" stroke-width="1.4"/><path d="M4 7.2l2 2 4-4.4" fill="none" stroke="var(--accent-red)" stroke-width="1.6"/></svg>Deck &amp; Patio Construction</li>
        <li class="services__item"><svg class="services__tick" viewBox="0 0 14 14" aria-hidden="true"><circle cx="7" cy="7" r="6" fill="none" stroke="var(--accent-red)" stroke-width="1.4"/><path d="M4 7.2l2 2 4-4.4" fill="none" stroke="var(--accent-red)" stroke-width="1.6"/></svg>Water &amp; Mold Damage</li>
        <li class="services__item"><svg class="services__tick" viewBox="0 0 14 14" aria-hidden="true"><circle cx="7" cy="7" r="6" fill="none" stroke="var(--accent-red)" stroke-width="1.4"/><path d="M4 7.2l2 2 4-4.4" fill="none" stroke="var(--accent-red)" stroke-width="1.6"/></svg>Garage Renovation</li>
      </ul>
    </div>
  </section>

</div>
</body>
</html>
```